i would like a business card to leave with customers and potential customers for electrical work and for the supply and install of reverse cycle airconditioning in the domestic and commercial market.
I own my own business and im a sole trader. I have an a'class electrical lisence and also a refrigeration lisence so i am
able to offer complete installations in airconditioning by a fully qualified and lisenced tradesman.
im looking for something that comes across as unique and professional.
i had the coluor black and some gold in mind but open to any coluors.
something like Lanterra Electrical & Refrigeration
or Lanterra Air.
i will use this design on a business card to advertise through summer to help generate installs through the busy season.

Target Market(s)

Mainly domestic house holds through summer who are in need of airconditioning and reliable information to acomadate thier cooling and heating requirements

Industry/Entity Type

Electrical

Requirements
Must have
• Business name- Lanterra
My name- Mark Delford
My mobile no- 0438 517 290
My email- mrdelford@qelvo.com.au
Installation & Decomissioning of aiconditioning split systems
LIC NO: TRK 540316
Nice to have
• Lanterra Electrical & Refrigeration

```html
<!DOCTYPE html>
<html lang="en">
<head>
<meta charset="utf-8">
<title>Lanterra Electrical &amp; Refrigeration – Business Card</title>
<link rel="stylesheet" href="https://fonts.googleapis.com/css2?family=Source+Sans+3:wght@400;600&display=swap">
<style>
  :root {
    --card-dark: #262f3a;
    --brand-blue: #2ea9df;
    --ink-white: #ffffff;
    --ink-dark: #1f2630;
  }
  * { margin: 0; padding: 0; box-sizing: border-box; }
  html, body { width: 999px; height: 1200px; overflow: hidden; background: var(--card-dark); }
  body { font-family: "Source Sans 3", "Myriad Pro", Arial, sans-serif; }
  .canvas { position: relative; width: 999px; height: 1200px; background: var(--card-dark); overflow: hidden; }
  .abs { position: absolute; line-height: 1; white-space: nowrap; }

  .card-divider { position: absolute; left: 0; top: 594px; width: 999px; height: 4px; background: var(--ink-white); }

  /* Front */
  .owner-name { left: 93px; top: 117px; font-size: 50px; color: var(--ink-white); }
  .owner-name .first { color: var(--brand-blue); }
  .name-chevron { position: absolute; left: 498px; top: 178px; }
  .contact-panel { position: absolute; left: 18px; top: 249px; }
  .contact-chevron { position: absolute; left: 64px; top: 349px; }
  .contact-line { left: 126px; font-size: 24px; color: var(--ink-white); }
  .contact-phone { top: 310px; }
  .contact-email { top: 346px; }
  .front-rule { position: absolute; left: 633px; top: 53px; width: 3px; height: 478px; background: var(--brand-blue); }
  .brand-mark-front { position: absolute; left: 690px; top: 62px; width: 100px; height: 100px; border-radius: 50%; background: var(--brand-blue); }
  .vertical-name { position: absolute; writing-mode: vertical-rl; color: var(--brand-blue); line-height: 1; white-space: nowrap; font-size: 48px; }
  .vertical-name.line-main { left: 900px; top: 89px; }
  .vertical-name.line-amp { left: 838px; top: 312px; }
  .vertical-name.line-sub { left: 770px; top: 169px; }

  /* Back */
  .brand-mark-back { position: absolute; left: 52px; top: 662px; width: 110px; height: 110px; border-radius: 50%; background: var(--brand-blue); }
  .back-name { font-size: 54px; color: var(--brand-blue); }
  .back-name.line-main { left: 260px; top: 641px; }
  .back-name.line-amp { left: 478px; top: 703px; }
  .back-name.line-sub { left: 338px; top: 765px; }
  .service-band { position: absolute; left: 0; top: 854px; width: 999px; height: 209px; background: var(--brand-blue); }
  .service-line { left: 101px; font-size: 54px; color: var(--ink-white); }
  .service-line.first { top: 893px; }
  .service-line.second { top: 964px; }
  .licence { right: 38px; top: 1122px; font-size: 45px; color: var(--ink-white); }
</style>
</head>
<body>
<main class="canvas">
  <!-- Front of card -->
  <section class="card-front">
    <p class="abs owner-name"><span class="first">Mark</span> Delford</p>
    <svg class="name-chevron" width="34" height="22" viewBox="0 0 34 22" aria-hidden="true">
      <polyline points="2,3 12,11 2,19" fill="none" stroke="#ffffff" stroke-width="4"/>
      <polyline points="17,3 27,11 17,19" fill="none" stroke="#2ea9df" stroke-width="4"/>
    </svg>
    <svg class="contact-panel" width="495" height="205" viewBox="0 0 495 205" aria-hidden="true">
      <polygon points="0,0 495,0 495,153 441,153 441,205 0,205" fill="#2ea9df"/>
    </svg>
    <svg class="contact-chevron" width="36" height="22" viewBox="0 0 36 22" aria-hidden="true">
      <polyline points="2,3 12,11 2,19" fill="none" stroke="#ffffff" stroke-width="4"/>
      <polyline points="17,3 27,11 17,19" fill="none" stroke="#1f2630" stroke-width="4"/>
    </svg>
    <p class="abs contact-line contact-phone">0438 517 290</p>
    <p class="abs contact-line contact-email">mrdelford@qelvo.com.au</p>
    <div class="front-rule"></div>
    <div class="brand-mark-front" aria-hidden="true"></div>
    <p class="vertical-name line-main">Lanterra Electrical</p>
    <p class="vertical-name line-amp">&amp;</p>
    <p class="vertical-name line-sub">Refrigeration</p>
  </section>

  <div class="card-divider"></div>

  <!-- Back of card -->
  <section class="card-back">
    <div class="brand-mark-back" aria-hidden="true"></div>
    <p class="abs back-name line-main">Lanterra Electrical</p>
    <p class="abs back-name line-amp">&amp;</p>
    <p class="abs back-name line-sub">Refrigeration</p>
    <div class="service-band"></div>
    <p class="abs service-line first">Installation &amp; Decomissioning</p>
    <p class="abs service-line second">of ariconditioning split systems</p>
    <p class="abs licence">LIC NO: TRK 540316</p>
  </section>
</main>
</body>
</html>
```